i need a business card for a plumbing company in california

we are a drain cleaning , maintenance plumbing company who is starting new marketing campaign for a tatrench-less pipe installation department .

Target Market(s)

the professional who appreciates time and quality workmanship.

Industry/Entity Type

Plumbing

Colors
0655a3
ec1f27

Requirements
Must have
• the second logo needs to be included
Nice to have
• a focus on the services offered
Should not have
• any underlined words on the brief

```html
<!DOCTYPE html>
<html lang="en">
<head>
<meta charset="utf-8">
<title>Crestline Plumbing – Business Card</title>
<link href="https://fonts.googleapis.com/css2?family=Arimo:wght@400;700&display=swap" rel="stylesheet">
<style>
  :root {
    --brand-red: #e0282a;
    --ink-grey: #6d6c66;
    --text-grey: #55554f;
    --card-white: #ffffff;
    --faint-red: #fbe6e2;
    --backdrop: #e4e4e2;
  }
  * { box-sizing: border-box; margin: 0; padding: 0; }
  html, body {
    width: 1200px; height: 880px; overflow: hidden;
    background: var(--backdrop);
    font-family: "Arimo", Arial, sans-serif;
  }
  .sheet {
    width: 1200px; height: 880px;
    display: flex; flex-direction: column; align-items: center; justify-content: center;
    gap: 44px;
  }
  .card {
    position: relative;
    width: 640px; height: 366px;
    border-radius: 18px;
    overflow: hidden;
    box-shadow: 0 6px 18px rgba(0,0,0,0.18);
  }
  /* Front */
  .card--front {
    background: var(--brand-red);
    display: flex; align-items: center; justify-content: center;
  }
  .brand-name {
    font-weight: 700;
    font-size: 46px;
    line-height: 1;
    letter-spacing: 0.5px;
  }
  .card--front .brand-name { color: var(--card-white); }
  /* Back */
  .card--back { background: var(--card-white); }
  .back-watermark {
    position: absolute; right: 40px; top: 18px;
    width: 210px; height: 210px; border-radius: 50%;
    background: var(--faint-red);
  }
  .back-brand {
    position: absolute; left: 44px; top: 70px;
    display: flex; align-items: center; gap: 12px;
  }
  .back-brand .brand-name { color: var(--ink-grey); font-size: 38px; }
  .brand-square {
    width: 26px; height: 26px; background: var(--brand-red);
  }
  .divider {
    position: absolute; left: 44px; right: 44px; top: 246px;
    height: 2px; background: var(--brand-red);
  }
  .person {
    position: absolute; left: 44px; top: 196px;
  }
  .person__name {
    color: var(--brand-red); font-weight: 700; font-size: 22px; line-height: 1.1;
  }
  .person__role {
    color: var(--text-grey); font-size: 15px; line-height: 1.2;
  }
  .address {
    position: absolute; right: 44px; top: 196px;
    text-align: right; color: var(--text-grey); font-size: 15px; line-height: 1.35;
  }
  .contacts {
    position: absolute; left: 44px; top: 262px;
    list-style: none;
    color: var(--text-grey); font-size: 16px; line-height: 1.55;
  }
  .contacts li { display: flex; align-items: center; gap: 8px; }
  .contacts svg { width: 14px; height: 14px; fill: var(--brand-red); flex: none; }
</style>
</head>
<body>
<main class="sheet">
  <section class="card card--front" aria-label="Card front">
    <span class="brand-name">Crestline Plumbing</span>
  </section>

  <section class="card card--back" aria-label="Card back">
    <div class="back-watermark" role="img" aria-label="Faint brand mark decoration"></div>
    <div class="back-brand">
      <span class="brand-name">Crestline Plumbing</span>
      <span class="brand-square"></span>
    </div>

    <div class="person">
      <p class="person__name">Dale Moreno</p>
      <p class="person__role">Manager</p>
    </div>

    <address class="address" style="font-style:normal">
      PO Box 48 Harbor Lane<br>Fresno
    </address>

    <div class="divider"></div>

    <ul class="contacts">
      <li>
        <svg viewBox="0 0 16 16" aria-hidden="true"><path d="M3.6 1.5l2.3 2.3c.4.4.4 1 0 1.4L4.7 6.4c.9 2 2.9 4 4.9 4.9l1.2-1.2c.4-.4 1-.4 1.4 0l2.3 2.3c.4.4.4 1 0 1.4l-1.3 1.3c-.8.8-2 .9-3 .4C6.6 13.9 2.1 9.4.5 5.8c-.5-1-.4-2.2.4-3L2.2 1.5c.4-.4 1-.4 1.4 0z"/></svg>
        555-014-2290
      </li>
      <li>
        <svg viewBox="0 0 16 16" aria-hidden="true"><path d="M1 3h14v10H1z M1.5 3.5L8 9l6.5-5.5" fill="none" stroke="#e0282a" stroke-width="1.6"/></svg>
        hello@crestlineplumb.com
      </li>
      <li>
        <svg viewBox="0 0 16 16" aria-hidden="true"><circle cx="8" cy="8" r="6.5" fill="none" stroke="#e0282a" stroke-width="1.4"/><path d="M1.5 8h13M8 1.5c-3 3.5-3 9.5 0 13M8 1.5c3 3.5 3 9.5 0 13" fill="none" stroke="#e0282a" stroke-width="1.2"/></svg>
        www.crestlineplumb.com
      </li>
    </ul>
  </section>
</main>
</body>
</html>
```